MRLC Needs Fundraiser Dinner Invite!!

The Marla Renquist Foundation, a 501 3(c) non for profit has a yearly fundraiser, with varying themes. Last year it was "cowboys" and "cowgirls"
This year, it is Parlor 19, or 70's disco music. I have uploaded last years invite for reference, some stock photography for inspiration. You are not limited to using the stock photos.

Annual MRLC Fundraiser Dinner
October 13th, 2022
Starts: 6:30pm
RSVP By: September 20th
Place: The Denbrook
Price: $135 per ticket

Target Market(s)

Donors, Business People, Every person

Industry/Entity Type

Non for Profit

Font styles to use
Sans Serif

Colors
0054AA
0677BA
7BADD7
CADEEF
E8F1F8
E54698
E96AAD
F1A4CE
F9D9EA
FCEFF6
6B429C
8869AF
B7A5CE
E3DAEB
F3F0F8

Requirements
Must have
• The invite should be 5x7, be sophisticated as the clientele are mainly business people that come to support the cause. It should be fun and inviting at the same time.

```html
<!DOCTYPE html>
<html lang="en">
<head>
<meta charset="utf-8">
<title>MRLC Annual Fundraiser Dinner Invitation</title>
<link rel="stylesheet" href="https://fonts.googleapis.com/css2?family=Tilt+Neon&family=Montserrat:wght@600;700;800&family=Caveat+Brush&family=Allura&family=Quicksand:wght@500&display=swap">
<style>
  :root {
    --bg-top: #9658e0;
    --bg-mid: #b08cf0;
    --bg-bottom: #d9d6f8;
    --ink: #4a2f6b;
    --white: #ffffff;
    --neon-pink: #ff5fa8;
    --script-pink: #f0389a;
    --pink-deep: #e0289b;
    --pink-soft: #f7a8d8;
    --disco-light: #b9e8f8;
    --disco-mid: #d88ae8;
    --disco-deep: #8a3fb8;
    --film-paper: #fdf0f2;
    --film-ink: #111111;
  }
  * { margin: 0; padding: 0; box-sizing: border-box; }
  html, body { width: 851px; height: 1200px; overflow: hidden; }
  body { background: var(--bg-bottom); }
  .invite {
    position: relative; width: 851px; height: 1200px; overflow: hidden;
    background: linear-gradient(180deg, var(--bg-top) 0%, var(--bg-mid) 45%, var(--bg-bottom) 100%);
    font-family: "Montserrat", sans-serif;
  }
  .deco { position: absolute; border-radius: 50%; }
  .white-sphere {
    left: -103px; top: -90px; width: 440px; height: 440px;
    background: radial-gradient(circle at 40% 40%, #ffffff 0%, #ececf0 60%, #d6d3dc 100%);
  }
  .pink-sphere {
    background: radial-gradient(circle at 35% 30%, #ffe2f2 0%, var(--pink-soft) 18%, var(--pink-deep) 65%, #b8137a 100%);
  }
  .disco-ball {
    background: radial-gradient(circle at 40% 35%, var(--disco-light) 0%, var(--disco-mid) 45%, var(--disco-deep) 100%);
  }
  .sphere-top { left: 182px; top: -55px; width: 240px; height: 240px; }
  .disco-left { left: -62px; top: 171px; width: 206px; height: 206px; }
  .disco-right { left: 717px; top: 600px; width: 186px; height: 186px; }
  .sphere-right { left: 596px; top: 706px; width: 330px; height: 330px; }
  .disco-bottom { left: -34px; top: 803px; width: 274px; height: 274px; }
  .sphere-bottom-left { left: -34px; top: 1029px; width: 164px; height: 164px; }
  .sphere-bottom { left: 125px; top: 996px; width: 340px; height: 340px; }
  .sphere-price { left: 113px; top: 968px; width: 178px; height: 178px; }

  .neon-title {
    position: absolute; left: 43px; top: 20px; width: 780px;
    font-family: "Tilt Neon", sans-serif; font-size: 64px; letter-spacing: 2px;
    color: var(--white); white-space: nowrap;
  }
  .neon-title span { text-shadow: 0 0 6px rgba(255,255,255,.8), 0 0 14px rgba(255,255,255,.5); }
  .neon-title .hot { color: var(--neon-pink); text-shadow: 0 0 6px rgba(255,95,168,.8), 0 0 14px rgba(255,95,168,.5); }

  .right-col { position: absolute; right: 84px; text-align: right; white-space: nowrap; }
  .lead { top: 124px; right: 55px; font-weight: 700; font-size: 29px; line-height: 48px; color: var(--white); }
  .hand { font-family: "Caveat Brush", sans-serif; color: var(--ink); }
  .annual { top: 222px; font-size: 62px; }
  .org-name { top: 288px; font-weight: 800; font-size: 150px; line-height: 150px; letter-spacing: -4px; color: var(--ink); }
  .org-full { top: 437px; font-weight: 600; font-size: 14px; letter-spacing: 2.4px; color: var(--ink); }
  .dinner { top: 460px; font-size: 60px; }

  .invited {
    position: absolute; left: 28px; top: 330px; transform: rotate(32deg);
    font-family: "Allura", cursive; font-size: 62px; line-height: 56px;
    color: var(--script-pink); white-space: nowrap;
  }

  .film-strip { position: absolute; left: 55px; top: 539px; width: 746px; height: 317px; background: var(--film-paper); }
  .film-label {
    position: absolute; left: 6px; top: 40px; writing-mode: vertical-rl;
    font-weight: 700; font-size: 11px; letter-spacing: 3px; color: var(--film-ink);
  }
  .frame-no { position: absolute; font-weight: 700; font-size: 11px; color: var(--film-ink); }
  .arrow { position: absolute; width: 0; height: 0; border-top: 4px solid transparent; border-bottom: 4px solid transparent; border-left: 14px solid var(--film-ink); }
  .photo { position: absolute; }
  .photo-one { left: 25px; top: 36px; width: 324px; height: 257px;
    background: linear-gradient(180deg, #b7aec8 0%, #d9d2e3 55%, #e8906a 85%, #c95640 100%); }
  .photo-two { left: 387px; top: 41px; width: 323px; height: 254px;
    background: linear-gradient(160deg, #8a7fa8 0%, #3c3446 50%, #c79ab0 85%, #e07458 100%); }

  .neon-sub {
    position: absolute; left: 187px; top: 877px; font-family: "Tilt Neon", sans-serif; font-size: 46px;
    letter-spacing: 3px; color: #ffe6f2; white-space: nowrap;
    text-shadow: 0 0 6px rgba(255,95,168,.9), 0 0 14px rgba(255,95,168,.6);
  }
  .date { top: 935px; font-size: 44px; }
  .venue { top: 1005px; font-size: 48px; }
  .doors { top: 1077px; font-size: 36px; }
  .rsvp { top: 1142px; font-weight: 700; font-size: 27px; letter-spacing: 4px; color: var(--ink); }

  .price {
    position: absolute; left: 140px; top: 1010px; transform: rotate(-14deg);
    font-family: "Quicksand", sans-serif; color: #fde6f2; text-align: center; line-height: 1;
  }
  .price .amount { display: block; font-size: 48px; letter-spacing: 2px; }
  .price .unit { display: block; font-size: 26px; letter-spacing: 2px; margin-top: 2px; }
</style>
</head>
<body>
<main class="invite">
  <div class="deco white-sphere" role="img" aria-label="Large pale silver sphere with a dotted pattern"></div>
  <div class="deco pink-sphere sphere-top" role="img" aria-label="Glossy pink balloon sphere"></div>
  <div class="deco disco-ball disco-left" role="img" aria-label="Pink and blue mirrored disco ball"></div>

  <h1 class="neon-title"><span>PARTY!</span> <span>PARTY!</span> <span class="hot">PARTY!</span></h1>

  <p class="right-col lead">COME AND JOIN US FOR A<br>RETRO PARTY TIME PARLOR 19</p>
  <p class="right-col hand annual">AT OUR ANNUAL</p>
  <p class="right-col org-name">MRLC</p>
  <p class="right-col org-full">THE MARLA RENQUIST FOUNDATION</p>
  <p class="right-col hand dinner">FUNDRAISER DINNER</p>

  <p class="invited">You're<br>&nbsp;&nbsp;Invited!</p>

  <section class="film-strip">
    <span class="film-label">LUMEN VISTA 400</span>
    <span class="arrow" style="left:20px;top:25px"></span>
    <span class="frame-no" style="left:188px;top:24px">2</span>
    <span class="arrow" style="left:328px;top:25px"></span>
    <span class="frame-no" style="left:539px;top:22px">2</span>
    <span class="arrow" style="left:712px;top:24px"></span>
    <span class="frame-no" style="left:184px;top:300px">2</span>
    <span class="arrow" style="left:323px;top:302px"></span>
    <span class="frame-no" style="left:535px;top:298px">2</span>
    <div class="photo photo-one" role="img" aria-label="Photo of silver disco balls in front of a silver tinsel curtain"></div>
    <div class="photo photo-two" role="img" aria-label="Photo of a person holding a disco ball beside a tinsel curtain"></div>
  </section>

  <div class="deco pink-sphere sphere-right" role="img" aria-label="Glossy pink balloon sphere"></div>
  <div class="deco disco-ball disco-right" role="img" aria-label="Pink mirrored disco ball"></div>
  <div class="deco disco-ball disco-bottom" role="img" aria-label="Blue and pink mirrored disco ball"></div>
  <div class="deco pink-sphere sphere-bottom-left" role="img" aria-label="Glossy pink balloon sphere"></div>
  <div class="deco pink-sphere sphere-bottom" role="img" aria-label="Glossy pink balloon sphere"></div>
  <div class="deco pink-sphere sphere-price" role="img" aria-label="Glossy pink balloon sphere"></div>

  <p class="neon-sub">70'S DISCO MUSIC</p>
  <p class="right-col hand date">OCTOBER 13TH, 2022</p>
  <p class="right-col hand venue">AT THE DENBROOK</p>
  <p class="right-col hand doors">DOORS OPEN AT 6:30 P.M.</p>
  <p class="right-col rsvp">RSVP by September 20th</p>

  <p class="price"><span class="amount">$135</span><span class="unit">per ticket</span></p>
</main>
</body>
</html>
```